Business Card Design - Amberfield Court

We are looking at a new design for our business cards that has a modern and professional look. We run a residential aged care facility focussing on the care of residents. The cards will be used for potential clients, consultants and business opportunities in this sector. Blue and white is our main colours and would to see these colours incorporated in the design.
Industry/Entity Type
Business
Contact Information for Business Card
Amberfield Court, Darren Walsh, dwalsh@amberfieldcourt.com.au, Finance Manager, 0472 639 208, BCom, 37 Marrabel Crescent, Brindle Vale, Qld 4093.
Look and feel
Each slider illustrates characteristics of the customer's brand and the style your logo design should communicate.

```html
<!DOCTYPE html>
<html lang="en">
<head>
<meta charset="utf-8">
<title>Amberfield Court – Business Card</title>
<link href="https://fonts.googleapis.com/css2?family=Open+Sans:wght@400;600&display=swap" rel="stylesheet">
<style>
  :root {
    --bg: #e9e7e4;
    --card: #ffffff;
    --blue: #3f7396;
    --tan: #b09d90;
    --ink: #3a3a3a;
    --rule: #8a8a8a;
  }
  * { box-sizing: border-box; margin: 0; padding: 0; }
  html, body {
    width: 1200px; height: 873px; overflow: hidden;
    background: var(--bg);
    font-family: "Open Sans", Arial, sans-serif;
  }
  .stage {
    width: 1200px; height: 873px;
    display: flex; align-items: center; justify-content: center; gap: 50px;
  }
  .card {
    position: relative;
    width: 525px; height: 300px;
    background: var(--card);
    box-shadow: 0 2px 10px rgba(0,0,0,.12);
  }

  /* Front */
  .card--front { display: flex; align-items: center; justify-content: center; }
  .brand { display: flex; flex-direction: column; align-items: center; }
  .brand__row { display: flex; align-items: center; gap: 14px; }
  .brand__dot { width: 44px; height: 44px; border-radius: 50%; background: var(--blue); }
  .brand__name {
    font-size: 28px; font-weight: 400; letter-spacing: 4px;
    text-transform: uppercase; color: var(--blue);
  }
  .brand__tagline {
    margin-top: 10px;
    font-size: 15px; color: var(--tan); letter-spacing: .5px;
  }

  /* Back */
  .card--back { padding: 40px 32px; }
  .back-brand { display: flex; align-items: center; gap: 9px; }
  .back-brand__dot { width: 22px; height: 22px; border-radius: 50%; background: var(--blue); }
  .back-brand__name {
    font-size: 14px; letter-spacing: 2px; text-transform: uppercase; color: var(--blue);
  }
  .back-brand__tagline { margin: 5px 0 0 31px; font-size: 9px; color: var(--tan); }
  .contact {
    position: absolute; left: 32px; right: 24px; bottom: 52px;
    display: flex; align-items: stretch;
    font-size: 9px; color: var(--ink); line-height: 1.6;
    white-space: nowrap;
  }
  .contact__block { padding: 0 12px; flex-shrink: 0; }
  .contact__block:first-child { padding-left: 0; }
  .contact__block + .contact__block { border-left: 1px solid var(--rule); }
  .contact__name { color: var(--blue); font-size: 10px; }
  .contact__label { font-weight: 600; }
</style>
</head>
<body>
<main class="stage">
  <section class="card card--front" aria-label="Business card front">
    <div class="brand">
      <div class="brand__row">
        <span class="brand__dot"></span>
        <span class="brand__name">Amberfield Court</span>
      </div>
      <p class="brand__tagline">Comfort, Respect, Wellbeing</p>
    </div>
  </section>

  <section class="card card--back" aria-label="Business card back">
    <div class="back-brand">
      <span class="back-brand__dot"></span>
      <span class="back-brand__name">Amberfield Court</span>
    </div>
    <p class="back-brand__tagline">Comfort, Respect, Wellbeing</p>

    <div class="contact">
      <div class="contact__block">
        <p class="contact__name">Amberfield Court, Darren Walsh</p>
        <p>Finance Manager</p>
      </div>
      <div class="contact__block">
        <p><span class="contact__label">M:</span> dwalsh@amberfieldcourt.com.au</p>
        <p><span class="contact__label">T:</span> 0472 639 208</p>
      </div>
      <div class="contact__block">
        <p><span class="contact__label">A:</span> 37 Marrabel Crescent,</p>
        <p>Brindle Vale, Qld 4093</p>
      </div>
    </div>
  </section>
</main>
</body>
</html>
```